I need a sophisticated and powerful book cover design that combines Japanese minimalism with contemporary appeal. The cover should convey personal transformation through the metaphor of a katana (Japanese sword).
Key Design Elements:
A katana, either partially shown or artistically rendered
Subtle Japanese design elements without being stereotypical
Clean, minimalist aesthetic
Professional font selection that bridges Eastern and Western typography
Color scheme: Deep blacks, steel grays, and possibly a touch of red or gold for accent
Mood/Style:
Professional and sophisticated
Blend of traditional Japanese aesthetics with modern design
Should appeal to personal development and business readers
Must convey strength and transformation
Elegant rather than aggressive
Specific Requirements:
Title: "The Lantern Compass"
Subtitle: "Quiet Methods for Growing Inner Steadiness and Calm Endurance"
Author names: Dorvelan Thaske and Meloda Thaske
Cover dimensions: Standard hardcover book size (6" x 9")
Must work well in both physical and digital thumbnail formats
Should be striking and legible when viewed as a small image online
Design Specifics:
Japanese elements such as brushstroke effects, kanji characters, or wave patterns
The design should reflect the book's core message: personal transformation through Japanese wisdom principles, using the katana as a metaphor for growth and development.

```html
<!DOCTYPE html>
<html lang="en">
<head>
<meta charset="utf-8">
<title>The Lantern Compass — Book Cover</title>
<link rel="stylesheet" href="https://fonts.googleapis.com/css2?family=Shojumaru&family=Russo+One&family=Open+Sans:wght@800&family=Arimo:ital,wght@1,700&family=Montserrat:wght@600&display=swap">
<style>
  :root {
    --page: #ffffff;
    --cover: #e6e8e7;
    --ink: #111111;
    --ink-soft: #333333;
    --navy: #2c394c;
    --red: #f21b12;
    --gold: #c98a3a;
    --pattern: #c9cbca;
    --steel-dark: #1a1a1a;
    --steel-mid: #8a8c8c;
  }
  html, body {
    margin: 0;
    width: 1200px;
    height: 1200px;
    overflow: hidden;
    background: var(--page);
  }
  .cover {
    position: absolute;
    left: 275px;
    top: 139px;
    width: 658px;
    height: 988px;
    background: var(--cover);
    overflow: hidden;
  }
  .wave-pattern {
    position: absolute;
    left: 394px;
    top: 0;
    width: 270px;
    height: 92px;
    background: radial-gradient(ellipse at 50% 0%, var(--pattern) 0%, rgba(201,203,202,0.5) 60%, transparent 72%);
  }
  .geo-pattern {
    position: absolute;
    background: radial-gradient(circle at 0% 50%, var(--pattern) 0%, rgba(201,203,202,0.45) 55%, transparent 72%);
  }
  .geo-pattern--left { left: 0; top: 429px; width: 110px; height: 205px; }
  .geo-pattern--right {
    left: 561px; top: 718px; width: 97px; height: 199px;
    background: radial-gradient(circle at 100% 50%, var(--pattern) 0%, rgba(201,203,202,0.45) 55%, transparent 72%);
  }
  .title {
    position: absolute;
    left: 0;
    top: 38px;
    width: 100%;
    margin: 0;
    text-align: center;
    font-weight: normal;
  }
  .title__lead {
    display: block;
    font-family: "Open Sans", sans-serif;
    font-weight: 800;
    font-size: 62px;
    line-height: 66px;
    color: var(--ink-soft);
  }
  .title__accent {
    display: block;
    margin-top: 6px;
    font-family: "Shojumaru", serif;
    font-size: 76px;
    line-height: 100px;
    color: var(--red);
    letter-spacing: 1px;
  }
  .title__main {
    display: block;
    margin-top: 8px;
    font-family: "Russo One", sans-serif;
    font-size: 84px;
    line-height: 96px;
    color: var(--ink);
    letter-spacing: 1px;
  }
  .subtitle {
    position: absolute;
    left: 40px;
    top: 336px;
    width: 578px;
    margin: 0;
    text-align: center;
    font-family: "Arimo", sans-serif;
    font-style: italic;
    font-weight: 700;
    font-size: 21px;
    line-height: 28px;
    color: var(--navy);
  }
  .subtitle em { font-style: italic; color: var(--red); }
  .sword-art {
    position: absolute;
    left: 241px;
    top: 426px;
    width: 230px;
    height: 509px;
    background:
      linear-gradient(90deg, transparent 38%, var(--steel-dark) 42%, var(--steel-mid) 50%, var(--steel-dark) 58%, transparent 62%),
      radial-gradient(ellipse at 50% 60%, rgba(120,120,120,0.35) 0%, transparent 65%);
    border-radius: 8px;
  }
  .red-dot {
    position: absolute;
    left: -7px;
    top: 925px;
    width: 62px;
    height: 62px;
    border-radius: 50%;
    background: var(--red);
  }
  .authors {
    position: absolute;
    left: 0;
    top: 940px;
    width: 100%;
    margin: 0;
    text-align: center;
    font-family: "Montserrat", sans-serif;
    font-weight: 600;
    font-size: 16px;
    letter-spacing: 4.5px;
    color: var(--gold);
    text-transform: uppercase;
  }
</style>
</head>
<body>
  <main class="cover">
    <div class="wave-pattern" role="img" aria-label="Japanese seigaiha wave pattern in light grey"></div>
    <div class="geo-pattern geo-pattern--left" role="img" aria-label="Geometric hexagonal ornament in light grey"></div>
    <div class="geo-pattern geo-pattern--right" role="img" aria-label="Geometric hexagonal ornament in light grey"></div>

    <h1 class="title">
      <span class="title__lead">THE</span>
      <span class="title__accent">LANTERN</span>
      <span class="title__main">COMPASS</span>
    </h1>

    <p class="subtitle">Quiet Methods for Growing Inner <em>Steadiness</em> and<br><em>Calm Endurance</em></p>

    <div class="sword-art" role="img" aria-label="Illustration of an upright sheathed katana wrapped in a flowing black ribbon with ink splatter"></div>

    <div class="red-dot"></div>

    <p class="authors">Dorvelan Thaske and Meloda Thaske</p>
  </main>
</body>
</html>
```